Brisbane IT support business needs our first website

Hi All,

We are after a new website design for our IT solutions and support business.The business name is Harbourline Computing Services Group, or HCSG for short. We provide a range of solutions and services within the IT space.

I would like to utilize the two colours in our business logo I have uploaded.

I understand this is initially for the design only aspect of the site, but I would like to engage the winner to finish coding the website and finalize after also.

Target Market(s)

Other businesses owners and home users.

Industry/Entity Type

Business

Requirements
Must have
• Nice clean and functional design utilizing our business colours from the logo.

```html
<!DOCTYPE html>
<html lang="en">
<head>
<meta charset="utf-8">
<title>HCSG – IT Solutions and Support</title>
<link href="https://fonts.googleapis.com/css2?family=Lato:wght@400;700;900&family=Open+Sans:wght@400;600;700&display=swap" rel="stylesheet">
<style>
:root{
  --navy:#1b3c6e;
  --navy-dark:#112847;
  --orange:#f7931e;
  --orange-dark:#e5801a;
  --ink:#333a44;
  --muted:#8a9099;
  --line:#e2e4e8;
  --band:#eeeff1;
  --footer:#1d1f23;
  --footer-deep:#141518;
  --white:#ffffff;
}
*{box-sizing:border-box;margin:0;padding:0}
html,body{width:1200px;height:2788px;overflow:hidden}
body{font-family:"Open Sans",Arial,sans-serif;color:var(--ink);background:var(--white);font-size:12px;line-height:1.6;position:relative}
.wrap{position:relative;width:860px;margin:0 auto}
h1,h2,h3,h4{font-family:"Lato",Arial,sans-serif}
.btn{display:inline-block;background:var(--navy-dark);color:var(--white);font-size:10px;padding:6px 14px;border-radius:2px;font-weight:600}

/* header */
.site-header{height:180px;border-bottom:1px solid var(--line)}
.topbar{height:34px;display:flex;justify-content:space-between;align-items:center;font-size:10px;color:var(--muted)}
.topbar .contact span{margin-right:18px}
.topbar .contact b{color:var(--orange)}
.social{display:flex;gap:8px}
.social i{display:block;width:14px;height:14px;background:#c9ccd1;border-radius:2px}
.navrow{display:flex;justify-content:space-between;align-items:center;height:140px}
.brand{display:flex;align-items:center;gap:14px}
.brand-mark{width:64px;height:64px;border-radius:50%;background:var(--navy)}
.brand-name{font-family:"Lato",sans-serif;font-weight:900;font-size:44px;color:var(--navy);letter-spacing:1px}
.main-nav{display:flex;gap:26px;font-family:"Lato",sans-serif;font-size:12px;font-weight:700;color:#555}
.main-nav .active{color:var(--orange)}

/* hero */
.hero{position:relative;height:520px;background:linear-gradient(100deg,#d7dde3 0%,#9aa9b6 38%,#4d6276 62%,#33465a 100%)}
.hero-copy{position:absolute;left:680px;top:150px;width:360px;color:var(--white)}
.hero-copy h1{font-size:42px;font-weight:700;line-height:1.15;margin-bottom:16px}
.hero-copy p{font-size:11px;color:#dfe5ea}
.hero-arrows{display:flex;gap:6px;margin-top:18px}
.hero-arrows svg{width:20px;height:20px}

/* welcome */
.welcome{height:280px;padding-top:40px}
.welcome .wrap{display:flex;gap:60px}
.laptop{width:220px;height:160px;background:linear-gradient(180deg,#2b3440,#5a6877);border-radius:6px}
.welcome-copy{width:580px}
.welcome-copy h2{font-size:26px;font-weight:700;color:var(--ink);line-height:1.2}
.welcome-copy h3{font-size:24px;font-weight:700;color:var(--orange);margin-bottom:14px;line-height:1.3}
.welcome-copy p{font-size:11px;color:var(--muted);margin-bottom:8px}

/* services */
.services{height:360px;background:var(--band);padding-top:20px}
.cards{display:flex;gap:20px}
.card{width:200px;height:320px;background:var(--white);text-align:center;padding:34px 16px 0}
.card.featured{background:var(--orange);color:var(--white)}
.card .icon{width:78px;height:78px;margin:0 auto 22px;border-radius:50%;background:var(--white);border:3px solid #d4d7db;display:flex;align-items:center;justify-content:center}
.card h4{font-size:14px;font-weight:700;margin-bottom:10px}
.card p{font-size:10px;color:var(--muted);margin-bottom:18px;line-height:1.7}
.card.featured p{color:#fff3e2}

/* projects */
.projects{height:340px;padding-top:30px}
.projects .wrap{display:flex;gap:30px}
.projects-intro{width:210px}
.projects-intro h2{font-size:18px;font-weight:900;color:var(--ink);margin-bottom:10px}
.projects-intro h2 span{color:var(--orange)}
.projects-intro p{font-size:10px;color:var(--muted);margin-bottom:20px}
.project-list{display:flex;gap:20px}
.project{width:193px}
.project .thumb{height:150px}
.project .caption{padding:12px 10px;background:var(--white);border:1px solid var(--line);border-top:none}
.project h4{font-size:13px;color:var(--navy);margin-bottom:4px}
.project p{font-size:10px;color:var(--muted)}

/* clients */
.clients{height:320px;background:linear-gradient(180deg,#f3f4f6 0%,#e1e4e8 100%);text-align:center;padding-top:36px}
.clients h2{font-size:26px;font-weight:700;color:var(--ink);margin-bottom:10px}
.clients p{font-size:10px;color:var(--muted);width:560px;margin:0 auto 34px}
.client-row{display:flex;justify-content:space-between}
.client{width:132px;height:52px;background:var(--white);display:flex;align-items:center;justify-content:center;font-family:"Lato",sans-serif;font-weight:700;font-size:15px;color:#555}

/* news & testimonials */
.lower{height:540px;padding-top:40px}
.lower .wrap{display:flex;gap:40px}
.section-title{font-size:18px;font-weight:700;color:var(--orange);padding-bottom:8px;border-bottom:1px solid var(--line);margin-bottom:20px}
.news{width:540px}
.news-list{display:flex;gap:30px}
.news-item{width:255px}
.news-item .thumb{height:130px;margin-bottom:12px}
.news-item h4{font-size:11px;color:var(--ink);margin-bottom:6px}
.meta{display:flex;align-items:center;gap:10px;font-size:9px;color:var(--muted);margin-bottom:8px}
.stars{color:var(--orange);letter-spacing:1px;font-size:11px}
.news-item p{font-size:10px;color:var(--muted)}
.testimonials{width:280px}
.quote{background:var(--band);padding:16px;font-size:10px;color:var(--muted);position:relative;margin-bottom:24px}
.quote:after{content:"";position:absolute;left:30px;bottom:-10px;border:10px solid transparent;border-top-color:var(--band);border-bottom:0}
.author{display:flex;align-items:center;gap:12px}
.avatar{width:54px;height:54px;border-radius:50%;background:linear-gradient(135deg,#6d7a88,#2f3b48)}
.author b{display:block;color:var(--orange);font-size:12px}
.author span{font-size:10px;color:var(--muted)}

/* footer */
.site-footer{position:absolute;left:0;top:2560px;width:1200px;height:228px;background:var(--footer);color:#c7cad0}
.footer-tab{position:absolute;left:560px;top:-20px;width:80px;height:20px}
.site-footer h2{text-align:center;color:var(--white);font-size:18px;font-weight:700;padding-top:12px}
.site-footer .lead{text-align:center;font-size:10px;color:#9aa0a8;margin-bottom:10px}
.contact-box{display:flex;gap:24px;width:860px;margin:0 auto;height:110px}
.office{width:250px;border:1px solid #3a3d43;padding:10px 14px;display:flex;gap:14px}
.office .brand-name{font-size:24px;color:var(--white)}
.office .brand-mark{width:34px;height:34px}
.office small{display:block;font-size:9px;line-height:1.5;color:#9aa0a8}
.office h4{font-size:11px;color:var(--white)}
.svc-list{width:150px;font-size:9px;line-height:1.45}
.svc-list h4{font-size:11px;color:var(--white);margin-bottom:2px}
.contact-form{flex:1;display:grid;grid-template-columns:1fr 1fr;gap:6px;align-content:start}
.contact-form i{display:block;height:18px;background:#2a2d33;border:1px solid #3a3d43}
.contact-form .msg{grid-column:2;grid-row:1 / span 3;height:66px}
.contact-form .send{grid-column:2;justify-self:center;background:var(--navy);color:var(--white);font-size:10px;padding:3px 22px;border-radius:2px}
.copyright{position:absolute;bottom:0;left:0;width:100%;height:24px;background:var(--footer-deep);font-size:9px;color:#7d838b;text-align:center;line-height:24px}
</style>
</head>
<body>

<header class="site-header">
  <div class="wrap topbar">
    <div class="contact"><span><b>T:</b> +61 7 3555 0142</span><span><b>E:</b> hello@hcsg-mail.net</span></div>
    <div class="social"><i></i><i></i><i></i><i></i></div>
  </div>
  <div class="wrap navrow">
    <div class="brand"><div class="brand-mark"></div><div class="brand-name">HCSG</div></div>
    <nav class="main-nav"><span class="active">HOME</span><span>ABOUT</span><span>SERVICES</span><span>WORKS</span><span>TEAM</span><span>BLOG</span><span>CONTACT</span></nav>
  </div>
</header>

<section class="hero" role="img" aria-label="Businessman looking through binoculars against a cloudy sky with faint technology graphics">
  <div class="hero-copy">
    <h1>IT Solutions and Support Company</h1>
    <p>We keep your business running with reliable networks, fast support and smart systems built around the way your team works every day.</p>
    <div class="hero-arrows">
      <svg viewBox="0 0 20 20"><circle cx="10" cy="10" r="10" fill="#1d1f23"/><path d="M12 5 7 10l5 5" stroke="#fff" stroke-width="2" fill="none"/></svg>
      <svg viewBox="0 0 20 20"><circle cx="10" cy="10" r="10" fill="#1d1f23"/><path d="m8 5 5 5-5 5" stroke="#fff" stroke-width="2" fill="none"/></svg>
    </div>
  </div>
</section>

<section class="welcome">
  <div class="wrap">
    <div class="laptop" role="img" aria-label="Laptop showing the company emblem on screen"></div>
    <div class="welcome-copy">
      <h2>Welcome To HCSG</h2>
      <h3>IT Solutions and Support</h3>
      <p>From a single home office to a growing business, our local technicians plan, install and look after the technology you rely on. We set up secure networks, manage backups and keep every device patched, so problems are solved before they slow you down.</p>
      <p>Talk with us about support plans, cloud migration or a one-off repair. Friendly advice, clear pricing and quick response times come standard with every job we take on.</p>
    </div>
  </div>
</section>

<section class="services">
  <div class="wrap cards">
    <article class="card featured">
      <div class="icon"><svg width="40" height="40" viewBox="0 0 40 40"><circle cx="20" cy="20" r="8" fill="none" stroke="#8a9099" stroke-width="4"/><circle cx="20" cy="20" r="15" fill="none" stroke="#8a9099" stroke-width="4" stroke-dasharray="6 4"/></svg></div>
      <h4>IT SOLUTIONS</h4>
      <p>Tailored hardware, software and network setups that grow with your business and budget.</p>
      <span class="btn">Read More</span>
    </article>
    <article class="card">
      <div class="icon"><svg width="40" height="40" viewBox="0 0 40 40"><rect x="5" y="6" width="30" height="22" fill="none" stroke="#8a9099" stroke-width="3"/><path d="M11 22v-6M17 22v-10M23 22v-4M29 22v-8M14 34h12" stroke="#8a9099" stroke-width="3"/></svg></div>
      <h4>Digital Marketing</h4>
      <p>Websites, search and email tools that bring new customers to your door each week.</p>
      <span class="btn">Read More</span>
    </article>
    <article class="card">
      <div class="icon"><svg width="40" height="40" viewBox="0 0 40 40"><rect x="6" y="6" width="28" height="20" fill="none" stroke="#8a9099" stroke-width="3"/><path d="M14 34h12M20 26v8" stroke="#8a9099" stroke-width="3"/></svg></div>
      <h4>System Maintenance</h4>
      <p>Regular health checks, updates and backups that keep every system safe and quick.</p>
      <span class="btn">Read More</span>
    </article>
    <article class="card">
      <div class="icon"><svg width="40" height="40" viewBox="0 0 40 40"><path d="M11 26a7 7 0 0 1 1-14 9 9 0 0 1 17 2 6 6 0 0 1 0 12z" fill="#8a9099"/><path d="M15 26v8M20 26v8M25 26v8" stroke="#8a9099" stroke-width="2"/></svg></div>
      <h4>Cloud Computing</h4>
      <p>Move files, email and apps to the cloud so your team can work from anywhere.</p>
      <span class="btn">Read More</span>
    </article>
  </div>
</section>

<section class="projects">
  <div class="wrap">
    <div class="projects-intro">
      <h2>RECENT <span>PROJECTS</span></h2>
      <p>A look at recent work for local clients, from office networks and server upgrades to new websites and cloud rollouts. Every project is planned, delivered and supported by our own team.</p>
      <span class="btn">Read More</span>
    </div>
    <div class="project-list">
      <article class="project"><div class="thumb" role="img" aria-label="Business team silhouettes around gears" style="background:linear-gradient(135deg,#9ea5ad,#4c535b)"></div><div class="caption"><h4>Advanced Features</h4><p>Network upgrade for a busy local office.</p></div></article>
      <article class="project"><div class="thumb" role="img" aria-label="Hand touching a glowing digital interface" style="background:linear-gradient(135deg,#b8c2cb,#3f4e5c)"></div><div class="caption"><h4>Advanced Features</h4><p>Cloud move for a regional retail group.</p></div></article>
      <article class="project"><div class="thumb" role="img" aria-label="Website platform theme on a dark background" style="background:linear-gradient(135deg,#3a3d42,#121316)"></div><div class="caption"><h4>Advanced Features</h4><p>New website for a family trade business.</p></div></article>
    </div>
  </div>
</section>

<section class="clients" role="region" aria-label="Our clients">
  <h2>Our Client</h2>
  <p>Businesses across the region trust us with their technology. We are proud to support these teams every day with dependable service and honest, practical advice.</p>
  <div class="wrap client-row">
    <div class="client">Marovia</div><div class="client">Nestpoint</div><div class="client">Airvale</div><div class="client">Ardlow</div><div class="client">Yarrow</div><div class="client">Altiva</div>
  </div>
</section>

<section class="lower">
  <div class="wrap">
    <div class="news">
      <h3 class="section-title">Recent News</h3>
      <div class="news-list">
        <article class="news-item">
          <div class="thumb" role="img" aria-label="Silhouettes of people working together on large gears" style="background:linear-gradient(180deg,#e8e8e8,#8d9298)"></div>
          <h4>NEW SUPPORT PLANS FOR SMALL TEAMS</h4>
          <div class="meta"><span>20 JUL 2024</span><span class="stars">★★★★☆</span></div>
          <p>Our new monthly plans give small offices unlimited help desk access, remote fixes and backups.</p>
        </article>
        <article class="news-item">
          <div class="thumb" role="img" aria-label="Close-up of a keyboard with a highlighted technology key" style="background:linear-gradient(135deg,#4f8fc7,#1b3c6e)"></div>
          <h4>WHY REGULAR BACKUPS MATTER</h4>
          <div class="meta"><span>12 JUL 2024</span><span class="stars">★★★★☆</span></div>
          <p>Simple steps every home user and business owner can take today to keep their files safe.</p>
        </article>
      </div>
    </div>
    <div class="testimonials">
      <h3 class="section-title">Testimonials</h3>
      <div class="quote">The team sorted out our whole office network in a single weekend. Fast, friendly and always there when we call with a question.<br><br><span style="color:#aaa">21 DAYS AGO</span></div>
      <div class="author"><div class="avatar" role="img" aria-label="Client portrait"></div><div><b>Mara Ellison</b><span>Practice Manager</span></div></div>
    </div>
  </div>
</section>

<footer class="site-footer">
  <svg class="footer-tab" viewBox="0 0 80 20"><path d="M0 20 40 0l40 20z" fill="#1d1f23"/></svg>
  <h2>Contact us</h2>
  <p class="lead">To book an appointment with one of our advisors, please contact one of our offices</p>
  <div class="contact-box">
    <div class="office">
      <div class="brand"><div class="brand-mark"></div><div class="brand-name">HCSG</div></div>
      <div><h4>Corporate Office</h4><small>18 Quay Lane, Suite 4<br>Riverside QLD 4000<br>+61 7 3555 0142<br>hello@hcsg-mail.net</small></div>
    </div>
    <div class="svc-list"><h4>Services</h4>Networking<br>IT Solutions<br>Cloud Computing<br>Maintenance<br>Web Design</div>
    <div class="contact-form"><i></i><i class="msg"></i><i></i><i></i><span class="send">Send</span></div>
  </div>
  <div class="copyright">© 2024 Harbourline Computing Services Group. All rights reserved.</div>
</footer>

</body>
</html>
```